Orvane Mechanical - Letterhead

We are a plumbing and hvac company based in Calgary. This letterhead will be on our quotes, invoices, preventative maintenance proposals etc.

```html
<!DOCTYPE html>
<html lang="en">
<head>
<meta charset="utf-8">
<title>Orvane Mechanical – Letterhead</title>
<link rel="stylesheet" href="https://fonts.googleapis.com/css2?family=Figtree:ital,wght@0,400;0,600;1,600;1,700&family=Work+Sans:wght@400&display=swap">
<style>
  :root {
    --backdrop: #e9e7e4;
    --paper: #ffffff;
    --brand-blue: #1f6fb8;
    --brand-orange: #ec5a24;
    --heading: #4a4a4a;
    --body: #767676;
    --footer-text: #2c2c2c;
    --signature-tone: #d9d9d9;
  }
  * { margin: 0; padding: 0; box-sizing: border-box; }
  html, body {
    width: 1185px; height: 1200px; overflow: hidden;
    background: var(--backdrop);
  }
  .letterhead {
    position: absolute; left: 168px; top: 0;
    width: 848px; height: 1200px;
    background: var(--paper);
    font-family: "Figtree", sans-serif;
    overflow: hidden;
  }
  .brand {
    position: absolute; left: 82px; top: 52px; width: 223px;
    display: flex; flex-direction: column; align-items: center;
  }
  .brand-dot {
    width: 74px; height: 74px; border-radius: 50%;
    background: var(--brand-orange);
  }
  .brand-name {
    margin-top: 18px;
    font-weight: 600; font-size: 21px;
    color: var(--brand-blue); letter-spacing: 0.5px; white-space: nowrap;
  }
  .greeting {
    position: absolute; left: 82px; top: 278px;
    font-size: 22px; font-weight: 600; color: var(--heading);
  }
  .body-copy {
    position: absolute; left: 82px; width: 686px;
    font-size: 13px; line-height: 21.4px; color: var(--body);
  }
  .body-copy .line {
    display: block; white-space: nowrap;
    text-align: justify; text-align-last: justify;
  }
  .p1 { top: 329px; } .p2 { top: 444px; } .p3 { top: 536px; } .p4 { top: 777px; }
  .signatory-name {
    position: absolute; left: 82px; top: 844px;
    font-size: 23px; font-weight: 600; font-style: italic; color: var(--heading);
  }
  .signatory-role {
    position: absolute; left: 82px; top: 878px;
    font-size: 13px; font-weight: 600; font-style: italic; color: var(--heading);
  }
  .signature {
    position: absolute; left: 82px; top: 924px; width: 219px; height: 73px;
    background: linear-gradient(90deg, var(--signature-tone), #ececec);
    border-radius: 4px;
  }
  .footer-rule {
    position: absolute; left: 82px; top: 1070px; width: 686px; height: 1.5px;
    background: var(--brand-orange);
  }
  .contact, .address {
    position: absolute; top: 1098px;
    font-family: "Work Sans", sans-serif; font-size: 13px; line-height: 17.2px;
    color: var(--footer-text); font-style: normal;
  }
  .contact { left: 82px; list-style: none; }
  .contact li { display: flex; align-items: center; gap: 5px; }
  .contact svg { width: 9px; height: 9px; fill: none; stroke: var(--brand-blue); stroke-width: 1.6; }
  .address { right: 80px; text-align: right; }
  .footer-band {
    position: absolute; left: 0; bottom: 0; width: 848px; height: 22px;
    background: var(--brand-blue);
    border-top: 5px solid var(--brand-orange);
    box-shadow: inset 0 2px 0 var(--paper);
  }
</style>
</head>
<body>
<main class="letterhead">
  <header class="brand">
    <div class="brand-dot"></div>
    <div class="brand-name">ORVANE MECHANICAL</div>
  </header>

  <h1 class="greeting">Dear sir/Madam,</h1>

  <p class="body-copy p1">
    <span class="line">Lorem ipsum dolor sit amet, consectetur adipiscing elit, sed do eiusmod tempor incididunt ut labore et</span>
    <span class="line">dolore magna aliqua. Ut enim ad minim veniam, quis nostrud exercitation ullamco laboris nisi ut aliquip ex</span>
    <span class="line">ea commodo consequat. Duis aute irure dolor in reprehenderit in voluptate velit esse cillum dolore eu</span>
    <span class="line">fugiat nulla pariatur. Excepteur sint occaecat cupidatat non proident, sunt in culpa qui officia deserunt</span>
  </p>

  <p class="body-copy p2">
    <span class="line">mollit anim id est laborum. Sed ut perspiciatis unde omnis iste natus error sit voluptatem accusantium</span>
    <span class="line">doloremque laudantium, totam rem aperiam, eaque ipsa quae ab illo inventore veritatis et quasi architecto</span>
    <span class="line">beatae vitae dicta sunt explicabo. Nemo enim ipsam voluptatem quia voluptas sit aspernatur aut odit aut</span>
  </p>

  <p class="body-copy p3">
    <span class="line">Neque porro quisquam est, qui dolorem ipsum quia dolor sit amet, consectetur, adipisci velit, sed quia non</span>
    <span class="line">numquam eius modi tempora incidunt ut labore et dolore magnam aliquam quaerat voluptatem. Ut enim ad minima</span>
    <span class="line">veniam, quis nostrum exercitationem ullam corporis suscipit laboriosam, nisi ut aliquid ex ea commodi</span>
    <span class="line">consequatur. Quis autem vel eum iure reprehenderit qui in ea voluptate velit esse quam nihil molestiae</span>
    <span class="line">consequatur, vel illum qui dolorem eum fugiat quo voluptas nulla pariatur. At vero eos et accusamus et</span>
    <span class="line">iusto odio dignissimos ducimus qui blanditiis praesentium voluptatum deleniti atque corrupti quos dolores</span>
    <span class="line">et quas molestias excepturi sint occaecati cupiditate non provident, similique sunt in culpa qui officia</span>
    <span class="line">deserunt mollitia animi, id est laborum et dolorum fuga. Et harum quidem rerum facilis est et expedita</span>
    <span class="line">distinctio. Nam libero tempore, cum soluta nobis est eligendi optio cumque nihil impedit quo minus id quod</span>
    <span class="line">maxime placeat facere possimus, omnis voluptas assumenda est, omnis dolor repellendus. Temporibus autem</span>
  </p>

  <p class="body-copy p4">
    <span class="line">quibusdam et aut officiis debitis aut rerum necessitatibus saepe eveniet ut et voluptates repudiandae sint</span>
    <span class="line">et molestiae non recusandae. Itaque earum rerum hic tenetur a sapiente delectus, ut aut reiciendis</span>
  </p>

  <div class="signatory-name">Dana Whitlock</div>
  <div class="signatory-role">Director</div>
  <div class="signature" role="img" aria-label="Handwritten signature of the director"></div>

  <div class="footer-rule"></div>
  <ul class="contact">
    <li><svg viewBox="0 0 10 10"><path d="M2 1 L4 1 L4.5 3 L3.3 4 Q4.5 6 6 6.7 L7 5.5 L9 6 L9 8 Q5 9 1.5 4.5 Q1 2.5 2 1Z"/></svg>(403) 555-0182</li>
    <li><svg viewBox="0 0 10 10"><rect x="1" y="2.5" width="8" height="5.5"/><path d="M1 2.5 L5 5.5 L9 2.5"/></svg>info@orvanemech.com</li>
    <li><svg viewBox="0 0 10 10"><circle cx="5" cy="5" r="4"/><path d="M1 5 H9 M5 1 Q2.5 5 5 9 M5 1 Q7.5 5 5 9"/></svg>www.orvanemech.com</li>
  </ul>
  <address class="address">2418 Kestrel Row SW<br>Calgary, AB T2P 1K3</address>

  <div class="footer-band" aria-hidden="true"></div>
</main>
</body>
</html>
```